Creating a website for a life changing company (Halvra Q)

We do need a website for our Coaching and Consulting business we recently launched. We do need it for information purposes and that our clients do have the opportunity to subscribe for packages, programs etc.
We would like to see designs which use the colours blue and yellow (see attachment). The final design should communicate our passion for the potential in people and the benefit (rising onward) for them.
Updates
Additional information:
Our company (webpage): Halvra Q (the C stands for "what people cannot see / imagine now...)
Welcome to Halvra Q(uarry)
Consulting (O.R.T.) & Coaching (Rise onward)
Two pillars:
1) O.R.T. ( Steward pathway - Our program - focussing on companies - business orientated)
2) Rise onward (Daily renewal - Events - focusing on individuals - primarily life changing)
For both of them we offer: Lanternhall & Halvra Q+ (This should go as a subscription)
Eventually you can draft this as a rhombus
Industry/Entity Type
Coaching / Consulting
Coding
Coded - Design and coding required
Number of Pages Required
1 page
Font styles to use
Other font styles liked:
- Lato
Requirements
Must have
- Please see attachment (About us / Offers / Calendar function / Links to plain circle and plain circle account / mailing list / page for clients
Nice to have
- A banner

```html
<!DOCTYPE html>
<html lang="en">
<head>
<meta charset="utf-8">
<title>Halvra Q — Coaching &amp; Consulting</title>
<link href="https://fonts.googleapis.com/css2?family=Lato:wght@400;700;900&display=swap" rel="stylesheet">
<style>
:root{
  --navy:#13284a;
  --navy-deep:#0d2140;
  --yellow:#f8c21b;
  --yellow-soft:#f6cd3a;
  --grey:#f0f0f0;
  --text:#3a3f4a;
  --muted:#9aa0a8;
  --white:#ffffff;
  --btn:linear-gradient(90deg,var(--yellow) 0%,#c9a12a 40%,var(--navy) 100%);
}
*{box-sizing:border-box;margin:0;padding:0}
html,body{width:1200px;height:4644px;overflow:hidden}
body{font-family:'Lato',sans-serif;color:var(--text);background:var(--white);position:relative}
section,footer{position:relative;width:1200px;overflow:hidden}
.abs{position:absolute}
.btn{position:absolute;display:flex;align-items:center;justify-content:center;border-radius:24px;background:var(--btn);color:var(--white);font-weight:700;font-size:12px;letter-spacing:.3px;text-transform:uppercase}
.photo{position:absolute;border-radius:50%}
.h2{position:absolute;font-weight:700;font-size:36px;color:var(--navy);text-transform:uppercase;letter-spacing:-.5px}
.h2.light{color:var(--white)}
.bar{position:absolute;width:34px;height:5px;background:var(--yellow)}
.copy{position:absolute;font-size:13px;line-height:25.5px;text-align:justify}

/* hero */
.hero{height:658px;background:linear-gradient(100deg,#eef0f1 0%,#e1e3e3 40%,#c9c5bd 100%)}
.brand{left:130px;top:30px;font-weight:700;font-size:17px;letter-spacing:5px;color:var(--navy);display:flex;align-items:center;gap:10px}
.brand i{width:22px;height:22px;border-radius:50%;background:var(--yellow);display:block}
.nav{left:388px;top:68px;display:flex;gap:27px;font-size:11.5px;font-weight:700;color:var(--navy)}
.nav span:first-child{border-bottom:2px solid var(--navy)}
.social{display:flex;gap:14px}
.social i{display:block;width:28px;height:28px;border-radius:50%;background:var(--navy);border:3px solid var(--yellow)}
.contact-btn{left:922px;top:10px;width:148px;height:42px;font-size:13px;text-transform:uppercase}
.hero-title{left:126px;top:215px;font-size:104px;font-weight:700;color:var(--navy);letter-spacing:-2px}
.hero-title em{font-style:normal;color:var(--yellow)}
.dots{left:574px;top:616px;display:flex;gap:5px}
.dots i{width:10px;height:10px;border-radius:50%;background:var(--navy);display:block}
.dots i:nth-child(2){background:var(--yellow)}

/* about */
.about{height:692px}
.about .panel{left:0;top:0;width:423px;height:692px;background:var(--yellow)}

/* programs */
.programs{height:645px;background:linear-gradient(180deg,var(--navy) 0%,#1b3050 100%)}
.card{position:absolute;top:162px;width:300px;height:398px;background:var(--white);border-radius:8px;text-align:center}
.card .img{position:absolute;left:6px;top:6px;width:288px;height:198px;border-radius:4px}
.card h3{position:absolute;top:225px;width:100%;font-size:15px;font-weight:700;color:var(--navy)}
.card .bar{left:133px;top:252px;height:3px}
.card p{position:absolute;left:14px;right:14px;top:262px;font-size:12.5px;line-height:25.5px}

/* calendar */
.calendar{height:625px}
.cal{left:605px;top:97px;width:463px;height:433px;background:var(--white);box-shadow:0 2px 14px rgba(0,0,0,.12);border-radius:4px}
.cal-head{position:absolute;left:60px;top:38px;font-size:16px;color:#222}
.cal-arrows{position:absolute;right:50px;top:36px;font-size:18px;color:#888;letter-spacing:26px}
.cal-grid{position:absolute;left:38px;top:100px;display:grid;grid-template-columns:repeat(7,40px);column-gap:15.7px;row-gap:15.5px;font-size:15px;text-align:center;color:#222}
.cal-grid b{font-weight:400;font-size:13px}
.cal-grid span{height:40px;line-height:40px;border-radius:8px}
.cal-grid .past{background:#f4f4f4;border:1px solid #e2e2e2;color:#b8b8b8}
.cal-grid .today{background:linear-gradient(135deg,var(--yellow),#7fa06a);color:var(--white)}
.cal-grid .next{color:#bbb}

/* offers */
.offers{height:582px;background:linear-gradient(180deg,#f3c93a 0%,#f6cd3e 100%)}
.offer{position:absolute;background:var(--navy);color:var(--white);border-radius:110px 0 110px 0}
.offer .label{position:absolute;font-size:24px;font-weight:700;text-transform:uppercase}
.offer .pct{position:absolute;font-size:96px;font-weight:700;color:var(--yellow);line-height:1}
.offer p{position:absolute;font-size:12.5px;line-height:25.5px;text-align:justify}

/* packages */
.packages{height:656px}
.pkg{position:absolute;top:180px;width:293px;height:378px;text-align:center}
.pkg .head{position:absolute;left:0;top:0;width:100%;height:108px;background:var(--grey)}
.pkg .kicker{position:absolute;top:30px;width:100%;font-size:15px;color:var(--navy);text-transform:uppercase}
.pkg .term{position:absolute;top:56px;width:100%;font-size:30px;font-weight:700;color:var(--yellow);text-transform:uppercase}
.pkg p{position:absolute;left:14px;right:14px;top:130px;font-size:12.5px;line-height:28px}
.pkg .btn{left:60px;top:304px;width:172px;height:47px;font-size:15px}
.pkg.featured{background:linear-gradient(180deg,var(--navy) 0%,#3e4a4e 45%,var(--yellow) 100%)}
.pkg.featured .head{background:transparent}
.pkg.featured .kicker,.pkg.featured .term,.pkg.featured p{color:var(--white)}
.pkg.featured .btn{background:var(--white);color:var(--navy)}

/* newsletter */
.newsletter{height:367px}
.newsletter .band{left:0;top:0;width:1080px;height:367px;background:var(--navy);border-radius:0 184px 184px 0}
.field{position:absolute;top:200px;width:248px;height:50px;border-radius:25px;background:var(--white);font-size:12px;color:#333;padding:18px 22px}

/* footer */
.site-footer{height:419px}
.foot-brand{left:128px;top:178px;font-size:34px;font-weight:700;letter-spacing:11px;color:var(--navy);display:flex;align-items:center;gap:14px}
.foot-brand i{width:30px;height:30px;border-radius:50%;background:var(--yellow);display:block}
.col{position:absolute;top:85px;font-size:13px;color:var(--navy)}
.col h4{font-size:15px;font-weight:700;margin-bottom:10px}
.col li{list-style:none;line-height:28px}
.col li::before{content:"» ";}
.rule{left:120px;top:325px;width:980px;height:1px;background:#555}
</style>
</head>
<body>

<section class="hero">
  <div class="abs" role="img" aria-label="Soft blurred office background" style="inset:0;background:linear-gradient(100deg,rgba(240,241,242,.9),rgba(210,206,198,.4))"></div>
  <div class="abs brand"><i></i>HALVRA Q</div>
  <div class="abs social" style="left:824px;top:16px"><i aria-label="Social profile link"></i><i aria-label="Professional network link"></i></div>
  <div class="btn contact-btn">Contact us</div>
  <nav class="abs nav"><span>HOME</span><span>ABOUT US</span><span>OFFERS</span><span>PACKAGES</span><span>PROGRAMS</span><span>CALENDAR</span><span>TESTIMONIALS</span><span>LANTERNHALL</span></nav>
  <h1 class="abs hero-title">Halvra <em>Q</em></h1>
  <p class="abs" style="left:132px;top:330px;width:430px;font-size:13px;line-height:27px">Lorem ipsum dolor sit amet, consectetur adipiscing elit, sed do eiusmod tempor incididunt ut labore et dolore magna aliqua. Ut enim ad minim veniam quis nostrud exercitation ullamco.</p>
  <div class="btn" style="left:132px;top:424px;width:146px;height:42px">Get started</div>
  <div class="photo" style="left:598px;top:128px;width:490px;height:490px;background:var(--yellow)"></div>
  <div class="photo" role="img" aria-label="Photo of a smiling businesswoman with folded arms in an office" style="left:624px;top:154px;width:438px;height:438px;background:linear-gradient(160deg,#d6d2c6,#a8b3c4 60%,#c8ccd2)"></div>
  <div class="abs dots"><i></i><i></i><i></i><i></i></div>
</section>

<section class="about">
  <div class="abs panel"></div>
  <div class="photo" style="left:138px;top:78px;width:490px;height:490px;background:#fff4c8;opacity:.8"></div>
  <div class="photo" role="img" aria-label="Portrait photo of a confident businessman in a suit" style="left:161px;top:101px;width:444px;height:444px;background:linear-gradient(160deg,#8fa8b8,#2f3d5a 65%,#56647a)"></div>
  <h2 class="h2" style="left:667px;top:106px;font-size:36px">About Marek</h2>
  <div class="bar" style="left:667px;top:160px"></div>
  <p class="copy" style="left:667px;top:180px;width:424px">Lorem ipsum dolor sit amet, consectetur adipiscing elit, sed do eiusmod tempor incididunt ut labore et dolore magna aliqua. Ut enim ad minim veniam, quis nostrud exercitation ullamco laboris nisi ut aliquip ex ea commodo consequat. Duis aute irure dolor in reprehenderit in voluptate velit esse cillum dolore eu fugiat nulla pariatur. Excepteur sint occaecat cupidatat non proident.</p>
  <p class="copy" style="left:667px;top:360px;width:424px">sunt in culpa qui officia deserunt mollit anim id est laborum omnis iste natus error sit voluptatem accusantium doloremque laudantium, totam rem aperiam, eaque ipsa quae ab illo inventore veritatis et quasi architecto beatae vitae dicta sunt explicabo. Nemo enim ipsam voluptatem quia voluptas sit aspernatur aut odit aut fugit, sed quia consequuntur magni dolores eos qui ratione.</p>
  <div class="btn" style="left:667px;top:532px;width:146px;height:44px">Learn more</div>
</section>

<section class="programs">
  <h2 class="h2 light" style="left:0;width:1200px;text-align:center;top:74px">Our Programs</h2>
  <div class="bar" style="left:583px;top:124px"></div>
  <div class="card" style="left:132px"><div class="img" role="img" aria-label="Photo of a coaching conversation between two women" style="background:linear-gradient(135deg,#7a6a5a,#c9b9a6)"></div><h3>COACHING</h3><div class="bar"></div><p>Lorem ipsum dolor sit amet, consectetur adipiscing elit, sed do eiusmod tempor incididunt ut labore et dolore magna aliqua.</p><div class="btn" style="left:77px;top:341px;width:146px;height:42px">Learn more</div></div>
  <div class="card" style="left:450px"><div class="img" role="img" aria-label="Photo of a consultant seated at a desk in an office" style="background:linear-gradient(135deg,#5d6670,#b8bec4)"></div><h3>CONSULTING</h3><div class="bar"></div><p>Lorem ipsum dolor sit amet, consectetur adipiscing elit, sed do eiusmod tempor incididunt ut labore et dolore magna aliqua.</p><div class="btn" style="left:77px;top:341px;width:146px;height:42px">Learn more</div></div>
  <div class="card" style="left:767px"><div class="img" role="img" aria-label="Photo of hands typing on a laptop with chat bubbles" style="background:linear-gradient(135deg,#d8d2d0,#9a8f92)"></div><h3>FIRESIDE CHAT</h3><div class="bar"></div><p>Lorem ipsum dolor sit amet, consectetur adipiscing elit, sed do eiusmod tempor incididunt ut labore et dolore magna aliqua.</p><div class="btn" style="left:77px;top:341px;width:146px;height:42px">Learn more</div></div>
</section>

<section class="calendar">
  <h2 class="h2" style="left:130px;top:127px">Our Calendar</h2>
  <div class="bar" style="left:130px;top:180px"></div>
  <p class="copy" style="left:130px;top:200px;width:426px">Lorem ipsum dolor sit amet, consectetur adipiscing elit, sed do eiusmod tempor incididunt ut labore et dolore magna aliqua. Ut enim ad minim veniam, quis nostrud exercitation ullamco laboris nisi ut aliquip ex ea commodo consequat. Duis aute irure dolor in reprehenderit in voluptate velit esse cillum dolore eu fugiat nulla pariatur. Excepteur sint occaecat cupidatat non proident.sunt in culpa qui officia deserunt mollit anim id est laborummnis iste natus error sit voluptatem accusantium doloremque laudantium, totam rem aperiam, eaque ipsa quae ab illo inventore .</p>
  <div class="btn" style="left:132px;top:448px;width:146px;height:44px">Learn more</div>
  <div class="abs cal">
    <div class="cal-head">May 2022</div>
    <div class="cal-arrows">‹›</div>
    <div class="cal-grid">
      <b>Su</b><b>Mo</b><b>Tu</b><b>We</b><b>Th</b><b>Fr</b><b>Sa</b>
      <span class="past">27</span><span class="past">28</span><span class="past">1</span><span class="past">2</span><span class="past">3</span><span class="past">4</span><span class="past">5</span>
      <span class="past">6</span><span class="past">7</span><span class="past">8</span><span class="past">9</span><span class="past">10</span><span class="past">11</span><span class="past">12</span>
      <span class="past">13</span><span class="today">14</span><span>15</span><span>16</span><span>17</span><span>18</span><span>19</span>
      <span>20</span><span>21</span><span>22</span><span>23</span><span>24</span><span>25</span><span>26</span>
      <span>27</span><span>28</span><span>29</span><span>30</span><span>31</span><span class="next">1</span><span class="next">2</span>
    </div>
  </div>
</section>

<section class="offers">
  <div class="abs" role="img" aria-label="Faint background photo of a smiling woman" style="inset:0;background:linear-gradient(90deg,rgba(255,255,255,0) 30%,rgba(210,170,60,.25) 70%,rgba(255,255,255,0))"></div>
  <h2 class="h2" style="left:0;width:1200px;text-align:center;top:68px">Our Offers</h2>
  <div class="bar" style="left:583px;top:120px;background:var(--navy)"></div>
  <div class="offer" style="left:-90px;top:162px;width:300px;height:310px">
    <p style="left:90px;top:34px;width:175px">secteur adipiscing elit, sed do labore et dolore magna aliqua. ices gravida. Risus commodo cus vel facilisis. Lorem ipsum piscing elit, sed do eiusmod dolore magna aliqua. Ut enim</p>
  </div>
  <div class="offer" style="left:255px;top:162px;width:690px;height:310px">
    <div class="label" style="left:72px;top:92px">Lorem ipsum</div>
    <div class="pct" style="left:62px;top:130px">50%</div>
    <p style="left:296px;top:34px;width:362px">Lorem ipsum dolor sit amet, consectetur adipiscing elit, sed do eiusmod tempor incididunt ut labore et dolore magna aliqua. Quis ipsum suspendisse ultrices gravida. Risus commodo viverra maecenas accumsan lacus vel facilisis. Lorem ipsum dolor sit amet, consectetur adipiscing elit, sed do eiusmod tempor incididunt ut labore et dolore magna aliqua. Ut enim ad minim veniam.</p>
    <div class="btn" style="left:297px;top:232px;width:146px;height:42px;background:var(--yellow)">Learn more</div>
  </div>
  <div class="offer" style="left:997px;top:162px;width:400px;height:310px">
    <div class="label" style="left:72px;top:92px">Lorem ipsum</div>
    <div class="pct" style="left:62px;top:130px">50%</div>
  </div>
</section>

<section class="packages">
  <h2 class="h2" style="left:0;width:1200px;text-align:center;top:94px">Our Packages</h2>
  <div class="bar" style="left:583px;top:146px"></div>
  <div class="pkg" style="left:132px"><div class="head"></div><div class="kicker">Rise Onward Light</div><div class="term">Half day</div><p>Lorem ipsum dolor sit amet, consectetur adipiscing elit, sed do eiusmod tempor incididunt ut labore et dolore magna aliqua. Ut enim ad minim veniam, quis nostrud exercitation ullamco laboris nisi ut aliquip ex ea commodo consequat.</p><div class="btn">Sign up</div></div>
  <div class="pkg featured" style="left:453px"><div class="head"></div><div class="kicker">Rise Onward</div><div class="term">2-3 Days</div><p>Lorem ipsum dolor sit amet, consectetur adipiscing elit, sed do eiusmod tempor incididunt ut labore et dolore magna aliqua. Ut enim ad minim veniam, quis nostrud exercitation ullamco laboris nisi ut aliquip ex ea commodo consequat.</p><div class="btn">Sign up</div></div>
  <div class="pkg" style="left:775px"><div class="head"></div><div class="kicker">Rise Onward Unlimited</div><div class="term">1 Week</div><p>Lorem ipsum dolor sit amet, consectetur adipiscing elit, sed do eiusmod tempor incididunt ut labore et dolore magna aliqua. Ut enim ad minim veniam, quis nostrud exercitation ullamco laboris nisi ut aliquip ex ea commodo consequat.</p><div class="btn">Sign up</div></div>
</section>

<section class="newsletter">
  <div class="abs band"></div>
  <div class="photo" style="left:840px;top:10px;width:350px;height:350px;background:var(--yellow)"></div>
  <div class="photo" role="img" aria-label="Photo of two women smiling while reading a tablet" style="left:862px;top:32px;width:322px;height:322px;background:linear-gradient(150deg,#c7c2bc,#6e6660 60%,#3d3b40)"></div>
  <h2 class="h2 light" style="left:0;width:910px;text-align:center;top:52px">Subscribe our newsletter</h2>
  <div class="bar" style="left:438px;top:102px"></div>
  <p class="abs" style="left:170px;width:570px;top:120px;font-size:12px;line-height:25px;color:var(--white);text-align:center">Lorem ipsum dolor sit amet, consectetur adipiscing elit, sed do eiusmod tempor incididunt ut labore et dolore magna aliquauis ipsum suspendisse ultrices gravida.</p>
  <div class="field" style="left:200px">First Name</div>
  <div class="field" style="left:462px">First Name</div>
  <div class="btn" style="left:382px;top:274px;width:146px;height:43px;background:var(--yellow)">Learn more</div>
</section>

<footer class="site-footer">
  <div class="abs foot-brand"><i></i>HALVRA Q</div>
  <div class="col" style="left:420px"><h4>QUICK LINKS</h4><ul><li>Home</li><li>Offers</li><li>Packages</li><li>Programs</li><li>Calendar</li><li>Testimonials</li><li>Lanternhall</li></ul></div>
  <div class="col" style="left:621px"><h4>LEGAL</h4><ul><li>Privacy Policy</li><li>Terms &amp; Conditions</li><li>About Us</li><li>Contact Us</li><li>FAQ</li></ul></div>
  <div class="col" style="left:843px;width:240px"><h4>CONTACT US</h4>
    <div style="display:flex;gap:12px;line-height:26px"><svg width="12" height="16" viewBox="0 0 12 16" style="margin-top:5px"><path d="M6 0a6 6 0 0 0-6 6c0 4.5 6 10 6 10s6-5.5 6-10a6 6 0 0 0-6-6zm0 8.5A2.5 2.5 0 1 1 6 3.5a2.5 2.5 0 0 1 0 5z" fill="#f8c21b"/></svg><span>123 Lorem ipsum dolor sit amet consectetur adipiscing elit.</span></div>
    <div style="display:flex;gap:12px;margin-top:8px;line-height:26px"><svg width="13" height="13" viewBox="0 0 24 24" style="margin-top:6px"><path d="M6.6 10.8a15.1 15.1 0 0 0 6.6 6.6l2.2-2.2a1 1 0 0 1 1-.25 11.4 11.4 0 0 0 3.6.57 1 1 0 0 1 1 1V20a1 1 0 0 1-1 1A17 17 0 0 1 3 4a1 1 0 0 1 1-1h3.5a1 1 0 0 1 1 1c0 1.25.2 2.45.57 3.6a1 1 0 0 1-.25 1z" fill="#f8c21b"/></svg><span>+1 555 010 4477</span></div>
    <div style="display:flex;gap:12px;margin-top:12px;line-height:26px"><svg width="14" height="11" viewBox="0 0 14 11" style="margin-top:8px"><rect width="14" height="11" rx="1" fill="#f8c21b"/><path d="M1 1l6 5 6-5" stroke="#fff" fill="none" stroke-width="1.3"/></svg><span>hello@halvraq.example</span></div>
    <div class="social" style="margin-top:18px;gap:12px"><i aria-label="Social profile link"></i><i aria-label="Social profile link"></i><i aria-label="Social profile link"></i><i aria-label="Social profile link"></i></div>
  </div>
  <div class="abs rule"></div>
  <p class="abs" style="left:0;width:1200px;text-align:center;top:360px;font-size:12.5px;color:#333">© Copyright 2022 <span style="color:var(--yellow);text-decoration:underline">HALVRA Q</span> &nbsp;| &nbsp;All Rights Reserved</p>
</footer>

</body>
</html>
```